Marwick Partners Exit Plan business consultant web site

This website is for a consulting business that helps other businesses with exit plans. Essentially, assists them with the sale of their business. This website should be very professional, almost with a wall street look. I would like a very attractive image on the homepage. Perhaps something that denotes success. Perhaps a picture of palm trees and a beach? I will leave it to you for interpretation.

Across the screen I would like the words "Does your business have an exit plan?"

Below that it should read the following:
Let us help you with a completely impartial, no obligation assessment (button with link to the contact page)

Also, please use logo in a prominent place on the website so it's easily seen.

Target Market(s)

Males 40+

Coding

Coded - Design and coding required

Number of Pages Required

5+ page

Colors

Designer to choose colors to be used in the design.

Requirements
Must have
• The tabs for the homepage on the top should be:
• 1. About us
• 2. Services
• 3. Industries
• 4. Our success
• 5. Contact
Nice to have
• Clean, professional image.
• Please put FB, Twitter, Linked In - logos at bottom.
• Here are two examples of a website to give you an idea:
• https://notes.quelvarocapital.example/library/why-every-business-owner-should-have-an-exit-plan
Should not have
• nothing whimsical or cartoon like

```html
<!DOCTYPE html>
<html lang="en">
<head>
<meta charset="utf-8">
<title>Marwick Partners — Exit Plan Consulting</title>
<link rel="stylesheet" href="https://fonts.googleapis.com/css2?family=IBM+Plex+Sans:wght@400;500;600;700&family=Lato:wght@400;700&display=swap">
<style>
:root{
  --ink:#111;
  --text:#333;
  --muted:#555;
  --white:#fff;
  --header-bg:#f7f7f7;
  --success-bg:#efefef;
  --field-bg:#efefef;
  --submit:#1e4a72;
  --footer-bar:#dcdcdc;
}
*{margin:0;padding:0;box-sizing:border-box}
html,body{width:1200px;height:3520px;overflow:hidden}
body{position:relative;background:var(--white);font-family:"Lato",sans-serif;color:var(--text)}
.abs{position:absolute}
.heading{font-family:"IBM Plex Sans",sans-serif;font-weight:700;color:var(--ink)}

/* header */
.site-header{left:0;top:0;width:1200px;height:105px;background:var(--header-bg)}
.brand{left:75px;top:0;width:319px;height:183px;background:var(--white);box-shadow:0 4px 14px rgba(0,0,0,.18);z-index:3;display:flex;flex-direction:column;align-items:center;justify-content:center;gap:14px}
.brand-square{width:78px;height:78px;background:var(--ink)}
.brand-name{font-family:"IBM Plex Sans",sans-serif;font-weight:500;font-size:25px;letter-spacing:2px;color:var(--ink);white-space:nowrap}
.main-nav{top:42px;left:490px;font-family:"IBM Plex Sans",sans-serif;font-weight:600;font-size:14px;color:#444}
.main-nav a{position:absolute;white-space:nowrap;color:inherit;text-decoration:none}
.home-link{left:4px;top:-4px;width:22px;height:30px;border-bottom:2px solid #333}

/* hero */
.hero{left:0;top:105px;width:1200px;height:570px;background:linear-gradient(110deg,#3a3d40 0%,#24282c 40%,#4a4f55 70%,#2d3136 100%)}
.hero-title{left:0;top:405px;width:1200px;text-align:center;font-size:40px;color:var(--white);letter-spacing:.5px;white-space:nowrap}
.hero-sub{left:174px;top:460px;width:850px;height:38px;background:rgba(0,0,0,.62);color:var(--white);font-size:20px;text-align:center;line-height:38px;white-space:nowrap}
.btn{display:flex;align-items:center;justify-content:center;gap:18px;background:#000;color:var(--white);border-radius:30px;font-family:"IBM Plex Sans",sans-serif;font-weight:600;text-decoration:none;white-space:nowrap}
.hero-btn{left:485px;top:525px;width:228px;height:52px;font-size:22px}
.hero-dots{left:556px;top:616px;width:88px;height:26px;background:rgba(60,60,60,.7);border-radius:13px;display:flex;align-items:center;justify-content:center;gap:14px}
.hero-dots span{width:6px;height:6px;border-radius:50%;background:var(--white)}

/* services */
.section-title{left:0;top:742px;width:1200px;text-align:center;font-size:38px;letter-spacing:1px}
.service{top:845px;width:310px;text-align:center}
.service svg{display:block;margin:0 auto}
.service h3{margin-top:30px;font-family:"IBM Plex Sans",sans-serif;font-weight:700;font-size:23px;line-height:28px;color:var(--ink);letter-spacing:.5px}
.service p{margin:22px auto 0;width:292px;font-size:11.5px;line-height:22px;color:var(--text)}
.service .arrow-dot{margin:26px auto 0;width:40px;height:40px;border-radius:50%;background:#000;display:flex;align-items:center;justify-content:center}

/* about */
.about{left:0;top:1262px;width:1200px;height:585px;background:linear-gradient(200deg,#123f5c 0%,#2a9aa3 35%,#1f5d8c 65%,#3a3978 100%);overflow:hidden}
.about-title{left:616px;top:1390px;font-size:40px;color:var(--white);letter-spacing:1px}
.about-text{left:613px;top:1453px;width:448px;font-size:18px;line-height:28px;color:var(--white)}
.about-btn{left:610px;top:1598px;width:201px;height:51px;font-size:18px}

/* stats */
.stat{top:1928px;width:340px;text-align:center}
.stat .num{font-family:"IBM Plex Sans",sans-serif;font-weight:700;font-size:54px;line-height:62px;color:var(--ink)}
.stat .label{margin-top:8px;font-family:"IBM Plex Sans",sans-serif;font-weight:600;font-size:23px;line-height:28px;color:var(--ink)}

/* success */
.success{left:0;top:2137px;width:1200px;height:518px;background:var(--success-bg)}
.success-title{left:131px;top:2240px;font-size:38px;letter-spacing:.5px}
.success-text{left:132px;top:2296px;width:455px;font-size:16.5px;line-height:27.6px;color:var(--text)}
.success-btn{left:131px;top:2523px;width:201px;height:52px;font-size:18px}
.success-video{left:612px;top:2239px;width:484px;height:328px;background:linear-gradient(135deg,#d8d2c4 0%,#9a8f7c 40%,#5a6470 75%,#c9c6bf 100%);box-shadow:0 3px 10px rgba(0,0,0,.25)}
.play{left:825px;top:2377px;width:58px;height:58px;border-radius:50%;background:#222;display:flex;align-items:center;justify-content:center}
.slide-arrow{top:2403px;width:36px;height:71px;background:#3a3a3a;display:flex;align-items:center;justify-content:center}
.slide-prev{left:40px;border-radius:36px 0 0 36px}
.slide-next{left:1126px;border-radius:0 36px 36px 0}

/* contact */
.contact-band{left:0;top:2655px;width:1200px;height:339px;background:linear-gradient(100deg,#2b2f33 0%,#3b4044 45%,#25292d 100%)}
.contact-title{left:0;top:2718px;width:1200px;text-align:center;font-family:"IBM Plex Sans",sans-serif;font-weight:400;font-size:38px;color:var(--white)}
.contact-sub{left:0;top:2772px;width:1200px;text-align:center;font-size:16px;color:#ddd}
.contact-card{left:145px;top:2813px;width:910px;height:322px;background:var(--white);box-shadow:0 2px 8px rgba(0,0,0,.2)}
.field{background:var(--field-bg);font-size:11px;color:#333;padding:10px 17px}
.field-name{left:206px;top:2853px;width:383px;height:34px}
.field-email{left:610px;top:2853px;width:382px;height:34px}
.field-msg{left:206px;top:2909px;width:786px;height:101px}
.submit{left:525px;top:3051px;width:150px;height:37px;background:var(--submit);color:var(--white);font-family:"IBM Plex Sans",sans-serif;font-weight:600;font-size:15px;display:flex;align-items:center;justify-content:center}

/* footer */
.footer-title{top:3197px;font-family:"IBM Plex Sans",sans-serif;font-weight:600;font-size:22px;color:#222}
.footer-list{list-style:none;font-size:14px;color:#222}
.footer-list li{height:33px;display:flex;align-items:center;gap:20px;white-space:nowrap}
.quick{left:80px;top:3240px}
.address{left:355px;top:3240px}
.contacts{left:647px;top:3240px}
.footer-brand{left:882px;top:3199px;width:220px;display:flex;flex-direction:column;align-items:center;gap:10px}
.footer-brand .brand-square{width:50px;height:50px}
.footer-brand .brand-name{font-size:16px;letter-spacing:1px}
.social{top:3328px;width:24px;height:24px;border-radius:50%;background:#111}
.footer-bar{left:0;top:3468px;width:1200px;height:52px;background:var(--footer-bar);font-size:13px;color:#222}
.footer-bar .copy{position:absolute;left:0;width:1200px;top:18px;text-align:center}
.footer-bar .mark{position:absolute;left:1117px;top:18px}
</style>
</head>
<body>

<header class="abs site-header"></header>
<div class="abs brand"><div class="brand-square"></div><div class="brand-name">MARWICK PARTNERS</div></div>
<nav class="abs main-nav">
  <a class="home-link" href="#"><svg width="18" height="16" viewBox="0 0 18 16"><path d="M9 1 L17 8 H14 V15 H10.5 V10.5 H7.5 V15 H4 V8 H1 Z" fill="#222"/></svg></a>
  <a href="#" style="left:53px">About Us</a>
  <a href="#" style="left:146px">Services</a>
  <a href="#" style="left:237px">Industries</a>
  <a href="#" style="left:340px">Our Success</a>
  <a href="#" style="left:456px">Contact</a>
</nav>

<section class="abs hero" role="img" aria-label="Photo of a businessman in glasses discussing plans with colleagues in an office"></section>
<h1 class="abs heading hero-title">DOES YOUR BUSINESS HAVE AN EXIT PLAN?</h1>
<p class="abs hero-sub">Let us help you with a completely impartial, no obligation assessment</p>
<a class="abs btn hero-btn" href="#">Contact Us</a>
<div class="abs hero-dots"><span></span><span></span><span></span></div>

<h2 class="abs heading section-title">SERVICES</h2>
<div class="abs service" style="left:105px">
  <svg width="104" height="100" viewBox="0 0 104 100" fill="none" stroke="#666" stroke-width="2">
    <rect x="4" y="20" width="84" height="64"/><path d="M32 20 V10 H60 V20"/><path d="M4 20 L46 52 L88 20"/>
    <path d="M40 46 L46 40 L52 46 L46 52 Z"/>
    <ellipse cx="78" cy="70" rx="22" ry="9"/><path d="M56 70 V86 M100 70 V86"/><path d="M56 86 A22 9 0 0 0 100 86"/><path d="M56 78 A22 9 0 0 0 100 78"/>
  </svg>
  <h3>WEALTH<br>PLANNING</h3>
  <p>Sed ut perspiciatis unde omnis iste natus error sit voluptatem accusantium doloremque laudantium, totam rem aperiam, eaque ipsa quae ab illo inventore veritatis et quasi architecto beatae.</p>
  <div class="arrow-dot"><svg width="8" height="10" viewBox="0 0 8 10"><path d="M2 1 L6 5 L2 9" stroke="#fff" stroke-width="1.8" fill="none"/></svg></div>
</div>
<div class="abs service" style="left:445px">
  <svg width="104" height="100" viewBox="0 0 104 100" fill="none" stroke="#666" stroke-width="2">
    <rect x="28" y="10" width="34" height="22"/><path d="M36 32 V40 L44 32"/><path d="M34 18 H56 M34 24 H50"/>
    <circle cx="26" cy="56" r="9"/><path d="M10 88 V78 A16 12 0 0 1 42 78 V88"/>
    <rect x="46" y="52" width="40" height="36"/><path d="M52 84 V74 M60 84 V68 M68 84 V72 M76 84 V62"/><path d="M52 68 L62 58 L70 62 L82 48"/>
  </svg>
  <h3>BUSINESS<br>CONSULTING</h3>
  <p>Sed ut perspiciatis unde omnis iste natus error sit voluptatem accusantium doloremque laudantium, totam rem aperiam, eaque ipsa quae ab illo inventore veritatis et quasi architecto beatae.</p>
  <div class="arrow-dot"><svg width="8" height="10" viewBox="0 0 8 10"><path d="M2 1 L6 5 L2 9" stroke="#fff" stroke-width="1.8" fill="none"/></svg></div>
</div>
<div class="abs service" style="left:788px">
  <svg width="104" height="100" viewBox="0 0 104 100" fill="none" stroke="#666" stroke-width="2.5">
    <rect x="12" y="64" width="12" height="24"/><rect x="32" y="52" width="12" height="36"/><rect x="52" y="40" width="12" height="48"/><rect x="72" y="28" width="12" height="60"/>
    <path d="M8 92 H90"/><path d="M12 50 L48 22"/><path d="M38 20 H50 V32"/>
  </svg>
  <h3>MARKETING<br>MANAGEMENT</h3>
  <p>Sed ut perspiciatis unde omnis iste natus error sit voluptatem accusantium doloremque laudantium, totam rem aperiam, eaque ipsa quae ab illo inventore veritatis et quasi architecto beatae.</p>
  <div class="arrow-dot"><svg width="8" height="10" viewBox="0 0 8 10"><path d="M2 1 L6 5 L2 9" stroke="#fff" stroke-width="1.8" fill="none"/></svg></div>
</div>

<section class="abs about">
  <svg class="abs" style="left:0;top:0" width="1200" height="585" viewBox="0 0 1200 585">
    <path d="M0 585 C40 420 200 330 420 300 C700 260 820 120 1000 90 C1110 72 1170 100 1200 120 V585 Z" fill="rgba(20,40,110,.28)"/>
    <path d="M760 0 C900 60 1050 40 1200 20 V0 Z" fill="rgba(255,255,255,.06)"/>
  </svg>
  <svg class="abs" style="left:120px;top:78px" width="372" height="390" viewBox="0 0 372 390" role="img" aria-label="Three rounded photo shapes showing colleagues laughing, a hand on a laptop and two women reviewing papers">
    <defs>
      <linearGradient id="ph1" x1="0" y1="0" x2="1" y2="1"><stop offset="0" stop-color="#e9e4dc"/><stop offset="1" stop-color="#7d8794"/></linearGradient>
      <linearGradient id="ph2" x1="0" y1="0" x2="1" y2="1"><stop offset="0" stop-color="#c9c2b8"/><stop offset="1" stop-color="#4b4f57"/></linearGradient>
    </defs>
    <path d="M92 2 C150 -6 222 30 222 90 C222 146 170 170 110 168 C40 166 2 140 4 100 C6 50 40 10 92 2 Z" fill="url(#ph1)"/>
    <path d="M240 120 C290 100 340 150 368 230 C388 300 330 360 280 350 C230 340 200 280 206 220 C210 170 216 132 240 120 Z" fill="url(#ph1)"/>
    <path d="M20 220 C70 170 150 180 200 230 C240 270 230 340 180 376 C120 410 20 380 2 330 C-10 290 0 240 20 220 Z" fill="url(#ph2)"/>
  </svg>
</section>
<h2 class="abs heading about-title" style="color:#fff">ABOUT US</h2>
<p class="abs about-text">We are Marwick Partners Exit Plan business consultant. We are a consulting business that helps other businesses with exit plans. Essentially, assists them with the sale of their business.</p>
<a class="abs btn about-btn" href="#">Learn More <svg width="8" height="12" viewBox="0 0 8 12"><path d="M2 1 L6 6 L2 11" stroke="#fff" stroke-width="2" fill="none"/></svg></a>

<div class="abs stat" style="left:72px"><div class="num">3000 +</div><div class="label">Marketing<br>Specializations</div></div>
<div class="abs stat" style="left:430px;top:1926px"><div class="num">24</div><div class="label">Professional<br>Certificates</div></div>
<div class="abs stat" style="left:792px"><div class="num">28</div><div class="label">Business<br>Consulting</div></div>

<section class="abs success"></section>
<h2 class="abs heading success-title">OUR SUCCESS</h2>
<p class="abs success-text">Sed ut perspiciatis unde omnis iste natus error sit voluptatem accusantium doloremque laudantium, totam rem aperiam, eaque ipsa quae ab illo inventore veritatis et quasi architecto beatae vitae dicta sunt explicabo. Nemo enim ipsam voluptatem quia voluptas sit aspernatur aut odit aut fugit, sed quia consequuntur magni dolores eos qui ratione voluptatem sequi nesciunt.</p>
<a class="abs btn success-btn" href="#">Learn More <svg width="8" height="12" viewBox="0 0 8 12"><path d="M2 1 L6 6 L2 11" stroke="#fff" stroke-width="2" fill="none"/></svg></a>
<div class="abs success-video" role="img" aria-label="Video still of a team working together at desks in a bright open-plan office"></div>
<div class="abs play"><svg width="16" height="20" viewBox="0 0 16 20"><path d="M2 1 L15 10 L2 19 Z" fill="#fff"/></svg></div>
<div class="abs slide-arrow slide-prev"><svg width="10" height="16" viewBox="0 0 10 16"><path d="M8 2 L2 8 L8 14" stroke="#fff" stroke-width="2.5" fill="none"/></svg></div>
<div class="abs slide-arrow slide-next"><svg width="10" height="16" viewBox="0 0 10 16"><path d="M2 2 L8 8 L2 14" stroke="#fff" stroke-width="2.5" fill="none"/></svg></div>

<section class="abs contact-band" role="img" aria-label="Dimmed photo of a man working at a laptop"></section>
<h2 class="abs contact-title">Contact Us</h2>
<p class="abs contact-sub">to contact us please use the form below</p>
<div class="abs contact-card"></div>
<div class="abs field field-name">Name*</div>
<div class="abs field field-email">Email*</div>
<div class="abs field field-msg">How May We Help You?</div>
<div class="abs submit">Submit</div>

<h3 class="abs footer-title" style="left:79px">Quick Links</h3>
<ul class="abs footer-list quick">
  <li><svg width="7" height="10" viewBox="0 0 7 10"><path d="M1.5 1 L5.5 5 L1.5 9" stroke="#222" stroke-width="1.8" fill="none"/></svg>Home</li>
  <li><svg width="7" height="10" viewBox="0 0 7 10"><path d="M1.5 1 L5.5 5 L1.5 9" stroke="#222" stroke-width="1.8" fill="none"/></svg>About</li>
  <li><svg width="7" height="10" viewBox="0 0 7 10"><path d="M1.5 1 L5.5 5 L1.5 9" stroke="#222" stroke-width="1.8" fill="none"/></svg>Services</li>
  <li><svg width="7" height="10" viewBox="0 0 7 10"><path d="M1.5 1 L5.5 5 L1.5 9" stroke="#222" stroke-width="1.8" fill="none"/></svg>Industries</li>
  <li><svg width="7" height="10" viewBox="0 0 7 10"><path d="M1.5 1 L5.5 5 L1.5 9" stroke="#222" stroke-width="1.8" fill="none"/></svg>Our Success</li>
  <li><svg width="7" height="10" viewBox="0 0 7 10"><path d="M1.5 1 L5.5 5 L1.5 9" stroke="#222" stroke-width="1.8" fill="none"/></svg>Contact</li>
</ul>

<h3 class="abs footer-title" style="left:357px">Address</h3>
<ul class="abs footer-list address">
  <li><svg width="12" height="16" viewBox="0 0 12 16"><path d="M6 15 C2 10 1 8 1 6 A5 5 0 0 1 11 6 C11 8 10 10 6 15 Z" fill="#222"/><circle cx="6" cy="6" r="2" fill="#fff"/></svg>#123 Lorium ipsum</li>
  <li style="padding-left:32px">Dolor amit,</li>
  <li style="padding-left:32px">Newzland-023</li>
</ul>

<h3 class="abs footer-title" style="left:648px">Contacts</h3>
<ul class="abs footer-list contacts">
  <li><svg width="16" height="12" viewBox="0 0 16 12"><rect x="1" y="1" width="14" height="10" fill="none" stroke="#222" stroke-width="1.6"/><path d="M1 1 L8 7 L15 1" fill="none" stroke="#222" stroke-width="1.6"/></svg>info@marwickpartners.example</li>
  <li><svg width="16" height="14" viewBox="0 0 16 16"><path d="M3 1 L6 1 L7 5 L5 6.5 C6 9 7 10 9.5 11 L11 9 L15 10 L15 13 C15 14 14 15 13 15 C6 15 1 10 1 3 C1 2 2 1 3 1 Z" fill="#222"/></svg>1-800 555 0142</li>
</ul>

<div class="abs footer-brand"><div class="brand-square"></div><div class="brand-name">MARWICK PARTNERS</div></div>
<a class="abs social" href="#" style="left:938px" aria-label="Social profile one"></a>
<a class="abs social" href="#" style="left:994px" aria-label="Social profile two"></a>
<a class="abs social" href="#" style="left:1050px" aria-label="Social profile three"></a>

<footer class="abs footer-bar"><span class="copy">© 2020 &nbsp;|&nbsp; www.marwickpartners.example</span><span class="mark">M1</span></footer>

</body>
</html>
```